Website for courses for men for making money, health, fitness

I require a website which is going to be a mix of a crypto currency website and website aimed at providing men with money making, health, relationship advice courses and content

The name isn't decided yet so for now please call it something like

KESTREL YARD

A platform dedicated to making men wealthy, physically strong, mentally tough & successful with women

In the top right, I need it to show how many points they have, they must buy points in order to use them to claim the courses.

WHAT WE DO

Kestrel yard is a platform where you can learn everything you need about business, making money, crypto currency, fitness, health, mental toughness and resilience and how to be successful with women all in one place

HOW WILL THIS WORK & WHY SHOULD I BUY POINTS?

xxxxxxxxxxxxxxxxxxxxxxxx
xxxxxxxxxxxxxxxxxxxxxxx
xxxxxxxxxxxxxxxxxxxxx

AFFILIATE SCHEME

EARN UP TO $125 DOLLARS PER PERSON WHO SIGNS UP THROUGH YOUR LINK

START EARNING NOW - button
______________________________________________________

BUY POINTS
(A maximum of only $250 worth of points can be purchased per person until the platform goes fully live)

ROAD MAP & THE MODEL

2023

Q1 - PRE BUY IN FOR POINTS

Q2 - FULL WEBSITE LAUNCH

Q3 - APP LAUNCH

Q4 - IN APP ADVERT LAUNCH

It must have a very slick and sharp eye catching look, and be designed to convert people into purchasing points

some ideas of the feel of the website -

https://brivaloo.io/
https://nestorly.style/
https://plumwick.trelvanta.com/

```html
<!DOCTYPE html>
<html lang="en">
<head>
<meta charset="utf-8">
<title>Kestrel Yard</title>
<link rel="stylesheet" href="https://fonts.googleapis.com/css2?family=Roboto:wght@300;400;500;700;900&family=Open+Sans:wght@400;600&display=swap">
<style>
:root{
  --bg:#181a2c;
  --header:#1f2031;
  --footer:#1c1c2e;
  --accent:#d690ef;
  --accent-dark:#1a1330;
  --white:#ffffff;
  --muted:#d8d8e4;
  --rule:#33344a;
  --q1:#3fa6e6;
  --q2:#c98be3;
  --q3:#f5b800;
  --q4:#e2483a;
}
*{margin:0;padding:0;box-sizing:border-box}
html,body{width:1200px;height:3769px;overflow:hidden;background:var(--bg);color:var(--white);font-family:"Open Sans",sans-serif}
.page{position:relative;width:1200px;height:3769px}
section,header,footer{position:absolute;left:0;width:1200px}
.abs{position:absolute}
.heading{position:absolute;font-family:"Roboto",sans-serif;font-weight:700;font-size:33px;line-height:40px;color:var(--white);white-space:nowrap}
.heading.center{left:0;width:1200px;text-align:center}
.underline{position:absolute;height:3px;width:108px;background:var(--accent)}
.btn{position:absolute;display:flex;align-items:center;justify-content:center;border-radius:25px;background:var(--accent);color:var(--accent-dark);font-family:"Roboto",sans-serif;font-weight:700;font-size:15px;letter-spacing:.2px;white-space:nowrap}
.btn-outline{background:transparent;border:2px solid var(--accent);color:var(--white)}
.logo{font-family:"Roboto",sans-serif;font-weight:300;color:var(--white);white-space:nowrap}

/* header */
.site-header{top:0;height:94px;background:var(--header)}
.site-header .logo{left:111px;top:24px;font-size:34px}
.nav a{position:absolute;top:36px;font-size:15px;color:var(--white);text-decoration:none;white-space:nowrap}
.points{left:875px;top:36px;font-size:15px;font-weight:700;display:flex;align-items:center;gap:6px;font-family:"Roboto",sans-serif}

/* hero */
.hero{top:94px;height:684px;background:radial-gradient(ellipse at 68% 45%,#3a2a8a 0%,#1e1a5a 35%,#12123a 70%,#0e0f2e 100%)}
.hero-art{left:585px;top:52px;width:440px;height:542px;border-radius:50%;background:radial-gradient(circle at 50% 45%,#c59a3a 0%,#6b3aa8 30%,#2a4fb8 55%,rgba(20,20,70,0) 75%)}
.hero .welcome{left:111px;top:200px;font-family:"Roboto",sans-serif;font-size:30px;font-weight:500}
.hero .title{left:111px;top:250px;font-family:"Roboto",sans-serif;font-size:70px;font-weight:700;line-height:1;white-space:nowrap}
.hero .lead{left:111px;top:345px;width:420px;font-size:15.5px;line-height:27px}
.dots{left:570px;top:626px;display:flex;gap:6px}
.dots span{width:11px;height:11px;border-radius:50%;background:var(--white)}
.dots span.on{background:var(--accent)}

/* what we do */
.what{top:778px;height:521px;background:var(--bg)}
.dot-grid{left:113px;top:93px;width:170px;height:160px;background-image:radial-gradient(circle,#4b4d64 2.5px,transparent 3px);background-size:26px 24.5px}
.what-ring{left:176px;top:86px;width:352px;height:352px;border-radius:50%;border:2px solid var(--accent)}
.what-art{left:182px;top:92px;width:338px;height:338px;border-radius:50%;background:radial-gradient(circle at 50% 40%,#b8f2ff 0%,#6ccde2 40%,#2c7f98 100%)}
.what .heading{left:600px;top:102px}
.what .underline{left:600px;top:149px}
.what .copy{left:600px;top:186px;width:486px;font-size:16.5px;line-height:30px;text-align:justify;color:var(--muted)}

/* how */
.how{top:1299px;height:556px;background:radial-gradient(ellipse at 50% 40%,#24385a 0%,#1a2744 55%,#141c34 100%)}
.how .heading{top:82px}
.how .underline{left:546px;top:127px}
.feature{position:absolute;top:190px;width:300px;text-align:center}
.feature svg{display:block;margin:0 auto}
.feature h3{font-family:"Roboto",sans-serif;font-weight:700;font-size:21px;margin-top:30px}
.feature p{font-size:14.5px;line-height:25px;margin-top:17px;color:var(--muted)}
.feature .btn{position:relative;margin:18px auto 0;width:124px;height:40px;font-size:14px}

/* affiliate */
.affiliate{top:1855px;height:380px;background:var(--bg)}
.affiliate .heading{top:82px}
.affiliate .underline{left:546px;top:128px}
.affiliate .copy{left:0;width:1200px;text-align:center;top:176px;font-size:19px;color:var(--muted)}
.affiliate .btn{left:502px;top:246px;width:196px;height:48px}

/* buy points */
.buy{top:2235px;height:299px;background:linear-gradient(180deg,#0e0e22 0%,#1d1240 45%,#3a1670 60%,#1d1240 80%,#0f0f24 100%)}
.buy-art{left:702px;top:40px;width:322px;height:220px;border-radius:50%;background:radial-gradient(ellipse at 50% 55%,#2f7bf0 0%,#1a4fc0 40%,rgba(30,40,120,0) 72%)}
.buy .heading{left:113px;top:40px}
.buy .underline{left:113px;top:83px}
.buy .copy{left:113px;top:114px;width:500px;font-size:17px;line-height:31px;color:var(--muted)}
.buy .btn{left:113px;top:205px;width:126px;height:47px;font-size:15px}

/* road map */
.roadmap{top:2534px;height:781px;background:var(--bg)}
.roadmap .heading{top:84px}
.roadmap .underline{left:546px;top:129px}
.photo-frame{left:120px;top:218px;width:417px;height:468px;background:var(--accent)}
.photo{left:111px;top:206px;width:417px;height:468px;background:linear-gradient(135deg,#e9e6e3 0%,#cfc8c0 45%,#8a7f76 100%)}
.year{left:790px;top:174px;width:100px;text-align:center;font-family:"Roboto",sans-serif;font-weight:700;font-size:22px}
.timeline{left:838px;top:228px;width:4px;height:427px;background:var(--white)}
.tick{position:absolute;left:834px;width:12px;height:12px;border-radius:50%;background:var(--white)}
.q{position:absolute;left:824px;width:32px;height:32px;border-radius:50%;border:2.5px solid var(--white);display:flex;align-items:center;justify-content:center;font-family:"Roboto",sans-serif;font-size:10px;font-weight:700;color:var(--white)}
.q-label{position:absolute;font-family:"Roboto",sans-serif;font-weight:500;font-size:21px;white-space:nowrap}

/* footer */
.site-footer{top:3315px;height:454px;background:var(--footer)}
.site-footer .logo{left:111px;top:160px;font-size:42px}
.follow{left:111px;top:252px;display:flex;align-items:center;gap:8px;font-size:18px}
.follow span{width:27px;height:27px;border-radius:50%;border:1.5px solid var(--white)}
.follow span:first-child{margin-left:6px}
.f-title{position:absolute;top:96px;font-family:"Roboto",sans-serif;font-weight:700;font-size:20px;white-space:nowrap}
.contact-item{position:absolute;left:430px;display:flex;align-items:center;gap:18px;font-size:14px;line-height:24px;white-space:nowrap}
.contact-item .ic{width:44px;height:44px;border-radius:50%;background:var(--accent);display:flex;align-items:center;justify-content:center;flex:none}
.contact-item b{font-weight:600;font-family:"Roboto",sans-serif;font-size:15px}
.f-list{position:absolute;top:150px;list-style:none;font-size:15px;line-height:26px;white-space:nowrap}
.divider{left:111px;top:372px;width:978px;height:1px;background:var(--rule)}
.copyright{left:0;width:1200px;top:396px;text-align:center;font-size:14px}
</style>
</head>
<body>
<div class="page">

<header class="site-header">
  <div class="abs logo">Kestrel Yard</div>
  <nav class="nav">
    <a style="left:382px">What We Do</a>
    <a style="left:507px">How It Work</a>
    <a style="left:631px">Buy Points</a>
    <a style="left:743px">Road Map</a>
  </nav>
  <div class="abs points">
    <svg width="17" height="17" viewBox="0 0 17 17"><circle cx="8.5" cy="8.5" r="7" fill="none" stroke="#fff" stroke-width="2"/><circle cx="8.5" cy="8.5" r="3.5" fill="#fff"/></svg>
    50
    <svg width="10" height="7" viewBox="0 0 10 7"><path d="M1 1l4 4 4-4" fill="none" stroke="#fff" stroke-width="1.6"/></svg>
  </div>
  <div class="btn" style="left:960px;top:22px;width:127px;height:48px">BUY POINTS</div>
</header>

<section class="hero">
  <div class="abs hero-art" role="img" aria-label="Glowing smartphone with a gold crypto coin and trading chart over a circuit platform"></div>
  <div class="abs welcome">Welcome to</div>
  <div class="abs title">Kestrel Yard</div>
  <p class="abs lead">A platform dedicated to making men wealthy, physically strong, mentally tough &amp; successful with women</p>
  <div class="btn" style="left:111px;top:428px;width:127px;height:49px">BUY POINTS</div>
  <div class="abs dots"><span></span><span class="on"></span><span></span><span></span></div>
</section>

<section class="what">
  <div class="abs dot-grid"></div>
  <div class="abs what-ring"></div>
  <div class="abs what-art" role="img" aria-label="Open hand holding a glowing medical cross"></div>
  <h2 class="heading">What We Do</h2>
  <div class="underline"></div>
  <p class="abs copy">Kestrel yard is a platform where you can learn everything you need about business, making money, crypto currency, fitness, health, mental toughness and resilience and how to be successful with women all in one place</p>
  <div class="btn" style="left:600px;top:338px;width:128px;height:49px">LEARN MORE</div>
</section>

<section class="how">
  <h2 class="heading center">How Will This Work &amp; Why Should I Buy Points?</h2>
  <div class="underline"></div>

  <div class="feature" style="left:84px">
    <svg width="96" height="96" viewBox="0 0 96 96" fill="none" stroke="#d690ef" stroke-width="3"><circle cx="36" cy="36" r="24"/><circle cx="36" cy="36" r="16"/><path d="M28 36l8-10 8 10-8 10z"/><ellipse cx="62" cy="58" rx="24" ry="18"/><circle cx="54" cy="56" r="4"/><circle cx="66" cy="52" r="4"/><circle cx="70" cy="64" r="4"/><path d="M20 62c4 14 24 22 42 14"/></svg>
    <h3>Crypto Tokens</h3>
    <p>Lorem ipsum dolor sit amet,<br>consectetur adipiscing elit, sed do</p>
    <div class="btn btn-outline">LEARN MORE</div>
  </div>

  <div class="feature" style="left:451px">
    <svg width="96" height="96" viewBox="0 0 96 96" fill="none" stroke="#d690ef" stroke-width="3"><circle cx="48" cy="30" r="22"/><circle cx="48" cy="30" r="15"/><path d="M53 23c-2-3-12-3-12 2s12 3 12 9-10 5-12 2M47 16v28"/><rect x="10" y="64" width="12" height="24"/><path d="M22 70h20c4 0 6 4 2 6H34m-12 8h30l30-16c-2-4-6-4-10-2l-16 8"/></svg>
    <h3>Money Making</h3>
    <p>Lorem ipsum dolor sit amet,<br>consectetur adipiscing elit, sed do</p>
    <div class="btn btn-outline">LEARN MORE</div>
  </div>

  <div class="feature" style="left:817px">
    <svg width="96" height="96" viewBox="0 0 96 96" fill="none" stroke="#d690ef" stroke-width="3"><path d="M48 84L16 52C2 38 10 14 30 14c8 0 14 4 18 10 4-6 10-10 18-10 12 0 20 8 22 18"/><path d="M10 48h18l6-12 8 24 6-12h10"/><circle cx="76" cy="52" r="12"/><path d="M76 45v14M69 52h14"/></svg>
    <h3>Health</h3>
    <p>Lorem ipsum dolor sit amet,<br>consectetur adipiscing elit, sed do</p>
    <div class="btn btn-outline">LEARN MORE</div>
  </div>
</section>

<section class="affiliate">
  <h2 class="heading center">Affiliate Scheme</h2>
  <div class="underline"></div>
  <p class="abs copy">Earn Up To $125 Dollars Per Person Who Signs Up Through Your Link</p>
  <div class="btn">START EARNING NOW</div>
</section>

<section class="buy">
  <div class="abs buy-art" role="img" aria-label="Two blue dollar coins floating over a purple digital wave"></div>
  <h2 class="heading">Buy Points</h2>
  <div class="underline"></div>
  <p class="abs copy">A maximum of only $250 worth of points can be purchased per person until the platform goes fully live</p>
  <div class="btn btn-outline">BUY POINT</div>
</section>

<section class="roadmap">
  <h2 class="heading center">Road Map &amp; The Model</h2>
  <div class="underline"></div>
  <div class="abs photo-frame"></div>
  <div class="abs photo" role="img" aria-label="Business partners shaking hands across a desk with a tablet"></div>

  <div class="abs year">2023</div>
  <div class="abs timeline"></div>
  <div class="tick" style="top:222px"></div>
  <div class="tick" style="top:650px"></div>

  <div class="q" style="top:265px;background:var(--q1)">Q1</div>
  <div class="q-label" style="left:887px;top:267px;color:var(--q1)">Pre Buy In For Points</div>

  <div class="q" style="top:369px;background:var(--q2)">Q2</div>
  <div class="q-label" style="right:414px;top:371px;color:var(--q2)">Full Website Launch</div>

  <div class="q" style="top:471px;background:var(--q3)">Q3</div>
  <div class="q-label" style="left:892px;top:473px;color:var(--q3)">App Launch</div>

  <div class="q" style="top:575px;background:var(--q4)">Q4</div>
  <div class="q-label" style="right:414px;top:577px;color:var(--q4)">In App Advert Launch</div>
</section>

<footer class="site-footer">
  <div class="abs logo">Kestrel Yard</div>
  <div class="abs follow">Follow <span></span><span></span><span></span></div>

  <div class="f-title" style="left:432px">Contact us</div>
  <div class="contact-item" style="top:155px">
    <div class="ic"><svg width="16" height="20" viewBox="0 0 16 20"><path d="M8 0a7 7 0 0 0-7 7c0 5 7 13 7 13s7-8 7-13a7 7 0 0 0-7-7z" fill="#fff"/><circle cx="8" cy="7" r="2.6" fill="#d690ef"/></svg></div>
    <div>Lorem ipsum dolor sit amet,<br>consectetur adipiscing</div>
  </div>
  <div class="contact-item" style="top:224px">
    <div class="ic"><svg width="18" height="18" viewBox="0 0 18 18"><path d="M4 1l3 4-2 2c1 3 3 5 6 6l2-2 4 3-2 3C8 17 1 10 1 3z" fill="#fff"/></svg></div>
    <div><b>Call Us</b><br>+1 555 014 2273</div>
  </div>
  <div class="contact-item" style="top:295px">
    <div class="ic"><svg width="18" height="14" viewBox="0 0 18 14"><rect width="18" height="14" rx="2" fill="#fff"/><path d="M1 2l8 6 8-6" fill="none" stroke="#d690ef" stroke-width="1.6"/></svg></div>
    <div><b>Email Us</b><br>info@kestrelyard.com</div>
  </div>

  <div class="f-title" style="left:761px">Menu</div>
  <ul class="f-list" style="left:761px"><li>What We Do</li><li>How It Work</li><li>Buy Points</li><li>Road Map</li></ul>

  <div class="f-title" style="left:944px">Other Links</div>
  <ul class="f-list" style="left:944px"><li>Terms &amp; Conditions</li><li>Privacy Policy</li><li>About Us</li><li>Support</li></ul>

  <div class="abs divider"></div>
  <div class="abs copyright">©Copyrights 2022 Kestrel Yard &nbsp;&nbsp;|&nbsp;&nbsp; All Rights Reserved</div>
</footer>

</div>
</body>
</html>
```